Frostvale Harborline LLC

we need a business card design

Industry/Entity Type

hvac

Contact Information for Business Card

my logo

Requirements
Must have
• my logo and same colors

```html
<!DOCTYPE html>
<html lang="en">
<head>
<meta charset="utf-8">
<title>Frostvale Harborline LLC – Business Card</title>
<link href="https://fonts.googleapis.com/css2?family=Montserrat:wght@400;500;700;800&display=swap" rel="stylesheet">
<style>
  :root {
    --stage: #3a3a3a;
    --card-blue: #1160ab;
    --sky: #1aaee5;
    --gold: #f7b844;
    --white: #ffffff;
  }
  * { box-sizing: border-box; margin: 0; padding: 0; }
  html, body { width: 1200px; height: 875px; overflow: hidden; }
  body {
    background: var(--stage);
    font-family: "Montserrat", Arial, sans-serif;
    color: var(--white);
    display: flex;
    align-items: center;
    justify-content: center;
    gap: 40px;
  }
  .card {
    position: relative;
    width: 540px;
    height: 309px;
    background: var(--card-blue);
    border-radius: 18px;
    overflow: hidden;
  }
  .edge-band {
    position: absolute;
    left: 0; bottom: 0;
    width: 100%; height: 24px;
  }
  .brand {
    display: flex;
    align-items: center;
    gap: 12px;
    font-weight: 800;
    color: var(--white);
    text-transform: uppercase;
    letter-spacing: 0.5px;
  }
  .brand-dot {
    flex: none;
    border-radius: 50%;
    background: var(--gold);
  }
  /* Front */
  .card-front .brand {
    position: absolute;
    left: 50%; top: 46%;
    transform: translate(-50%, -50%);
    font-size: 26px;
    line-height: 1.15;
    white-space: nowrap;
  }
  .card-front .brand-dot { width: 22px; height: 22px; }
  /* Back */
  .card-back .brand {
    position: absolute;
    right: 34px; top: 40px;
    font-size: 15px;
    line-height: 1.2;
    text-align: right;
  }
  .card-back .brand-dot { width: 14px; height: 14px; }
  .divider {
    position: absolute;
    left: 30px; right: 34px; top: 150px;
    height: 1px;
    background: var(--sky);
  }
  .person {
    position: absolute;
    left: 30px; top: 112px;
  }
  .person-name {
    font-size: 21px;
    font-weight: 700;
    text-transform: uppercase;
    letter-spacing: 0.3px;
  }
  .person-name .first { color: var(--sky); }
  .person-name .last { color: var(--gold); }
  .person-role {
    position: absolute;
    left: 30px; top: 158px;
    font-size: 13px;
    font-weight: 500;
  }
  .contact-list {
    position: absolute;
    left: 30px; top: 190px;
    list-style: none;
    font-size: 12.5px;
    font-weight: 500;
  }
  .contact-list li {
    display: flex;
    align-items: center;
    gap: 8px;
    margin-bottom: 8px;
  }
  .contact-list svg { width: 12px; height: 12px; flex: none; }
  .address {
    position: absolute;
    right: 34px; top: 190px;
    text-align: right;
    font-size: 12.5px;
    font-weight: 500;
    line-height: 1.55;
  }
</style>
</head>
<body>

  <section class="card card-front" aria-label="Business card front">
    <div class="brand"><span class="brand-dot"></span><span>Frostvale<br>Harborline LLC</span></div>
    <svg class="edge-band" viewBox="0 0 540 24" preserveAspectRatio="none" aria-hidden="true">
      <polygon points="0,16 330,16 322,24 0,24" fill="var(--sky)"/>
      <polygon points="340,6 540,6 540,24 322,24" fill="var(--gold)"/>
    </svg>
  </section>

  <section class="card card-back" aria-label="Business card back">
    <div class="brand"><span class="brand-dot"></span><span>Frostvale<br>Harborline LLC</span></div>

    <div class="person">
      <p class="person-name"><span class="first">Dorian</span> <span class="last">Pell</span></p>
    </div>
    <div class="divider"></div>
    <p class="person-role">Founder</p>

    <ul class="contact-list">
      <li>
        <svg viewBox="0 0 12 12" aria-hidden="true"><path d="M2.5 1 L4.5 1 L5.2 3.6 L4 4.6 C4.7 6 6 7.3 7.4 8 L8.4 6.8 L11 7.5 L11 9.5 C11 10.3 10.3 11 9.5 11 C5 11 1 7 1 2.5 C1 1.7 1.7 1 2.5 1Z" fill="var(--gold)"/></svg>
        <span>555.014.0277</span>
      </li>
      <li>
        <svg viewBox="0 0 12 12" aria-hidden="true"><rect x="0.5" y="2" width="11" height="8" rx="1" fill="var(--gold)"/><path d="M1 2.6 L6 6.5 L11 2.6" stroke="var(--card-blue)" stroke-width="1" fill="none"/></svg>
        <span>info@frostvaleharborline.com</span>
      </li>
      <li>
        <svg viewBox="0 0 12 12" aria-hidden="true"><circle cx="6" cy="6" r="5" fill="none" stroke="var(--gold)" stroke-width="1.2"/><ellipse cx="6" cy="6" rx="2.2" ry="5" fill="none" stroke="var(--gold)" stroke-width="1"/><line x1="1" y1="6" x2="11" y2="6" stroke="var(--gold)" stroke-width="1"/></svg>
        <span>www.frostvaleharborline.com</span>
      </li>
    </ul>

    <p class="address">12/40 Quarry Bend Rd<br>Marlow Heath ABC 4120</p>

    <svg class="edge-band" viewBox="0 0 540 24" preserveAspectRatio="none" aria-hidden="true">
      <polygon points="0,16 330,16 322,24 0,24" fill="var(--sky)"/>
      <polygon points="340,6 540,6 540,24 322,24" fill="var(--gold)"/>
    </svg>
  </section>

</body>
</html>
```